Rollers & Glides.com

Vertical Business Card with focus on branding with our icon. Information on card will be logo, persons name, position, phone number, email address and website. Use the the name Marcus Pellow, position President, phone number 480.915.2267, email Marcus@rollersandglides-demo.com, website www.rollersandglides-demo.com.

```html
<!DOCTYPE html>
<html lang="en">
<head>
<meta charset="utf-8">
<title>Rollers &amp; Glides — Business Card</title>
<link rel="stylesheet" href="https://fonts.googleapis.com/css2?family=Montserrat:wght@400;500&family=Open+Sans:wght@600&display=swap">
<style>
  :root {
    --page-bg: #e4e8ee;
    --band-blue-dark: #2c5a96;
    --band-blue-light: #4b79b4;
    --silver-light: #eef0f2;
    --silver-mid: #c9ced4;
    --silver-warm: #d9d2b8;
    --brand-blue: #2f5e9e;
    --gold: #d3c08e;
    --cream: #efe4c8;
    --contact-white: #eef2f8;
  }
  * { margin: 0; padding: 0; box-sizing: border-box; }
  html, body {
    width: 1200px;
    height: 1055px;
    overflow: hidden;
    background: var(--page-bg);
  }
  .canvas {
    position: relative;
    width: 1200px;
    height: 1055px;
  }
  .business-card {
    position: absolute;
    left: 340px;
    top: 72px;
    width: 520px;
    height: 910px;
    display: flex;
    flex-direction: column;
    box-shadow: 0 10px 30px rgba(30, 50, 80, 0.18);
  }
  .header-band {
    height: 158px;
    background: linear-gradient(180deg, var(--band-blue-dark), var(--band-blue-light));
    display: flex;
    align-items: flex-end;
    justify-content: center;
    padding-bottom: 30px;
  }
  .header-name {
    font-family: "Open Sans", sans-serif;
    font-weight: 600;
    font-size: 34px;
    letter-spacing: 0.5px;
    color: var(--cream);
  }
  .brand-band {
    position: relative;
    height: 398px;
    display: flex;
    align-items: center;
    justify-content: center;
    gap: 16px;
  }
  .brand-texture {
    position: absolute;
    inset: 0;
    background: linear-gradient(120deg, var(--silver-mid) 0%, var(--silver-light) 40%, var(--silver-mid) 65%, var(--silver-warm) 100%);
  }
  .brand-dot {
    position: relative;
    width: 40px;
    height: 40px;
    border-radius: 50%;
    background: var(--brand-blue);
    flex: none;
  }
  .brand-name {
    position: relative;
    font-family: "Open Sans", sans-serif;
    font-weight: 600;
    font-size: 40px;
    color: var(--brand-blue);
    white-space: nowrap;
  }
  .info-band {
    position: relative;
    height: 354px;
    background: linear-gradient(180deg, var(--band-blue-dark), var(--band-blue-light));
  }
  .person {
    position: absolute;
    right: 50px;
    top: 44px;
    text-align: right;
    font-family: "Montserrat", sans-serif;
  }
  .person-name {
    font-weight: 500;
    font-size: 34px;
    letter-spacing: 1px;
    color: var(--gold);
    line-height: 1.1;
  }
  .person-title {
    font-weight: 400;
    font-size: 27px;
    letter-spacing: 1px;
    color: var(--gold);
    line-height: 1.3;
  }
  .contact-list {
    position: absolute;
    left: 54px;
    top: 200px;
    list-style: none;
    font-family: "Montserrat", sans-serif;
    font-weight: 400;
    font-size: 23px;
    line-height: 31px;
    color: var(--contact-white);
  }
</style>
</head>
<body>
  <main class="canvas">
    <article class="business-card">
      <header class="header-band">
        <span class="header-name">Rollers &amp; Glides</span>
      </header>
      <section class="brand-band">
        <div class="brand-texture" role="img" aria-label="Frosted silver textured surface"></div>
        <span class="brand-dot"></span>
        <span class="brand-name">Rollers &amp; Glides</span>
      </section>
      <section class="info-band">
        <div class="person">
          <p class="person-name">Marcus Pellow</p>
          <p class="person-title">President</p>
        </div>
        <ul class="contact-list">
          <li>480.915.2267</li>
          <li>Marcus@rollersandglides-demo.com</li>
          <li>www.rollersandglides-demo.com</li>
        </ul>
      </section>
    </article>
  </main>
</body>
</html>
```